Mental Health Clinic Website

website for a mental health clinic. two files describing the website are attached, in case of conflicting info the word document is priority.

Target Market(s)

Ohio / Pennsylvania residents

Industry/Entity Type

Health Care

Coding

Coded - Design and coding required

Number of Pages Required

5+ page

Requirements
Must have
• see attached

```html
<!DOCTYPE html>
<html lang="en">
<head>
<meta charset="utf-8">
<title>Dr Halvorsen Serenity Center</title>
<link href="https://fonts.googleapis.com/css2?family=Open+Sans:wght@400;600;700;800&display=swap" rel="stylesheet">
<style>
:root{
  --orange:#f26522;
  --green:#5aa83c;
  --blue:#1f4fa8;
  --red:#e8303a;
  --ink:#1b1b1b;
  --text:#444;
  --footer:#1e1e1e;
  --white:#fff;
  --card:#eeeeee;
}
*{box-sizing:border-box;margin:0;padding:0}
html,body{width:1200px;height:4592px;overflow:hidden}
body{font-family:'Open Sans',Arial,sans-serif;color:var(--text);background:var(--white);position:relative}
section,header,footer{position:absolute;left:0;width:1200px}

/* header */
.site-header{top:0;height:115px;background:var(--white)}
.brand{position:absolute;left:168px;top:24px;display:flex;align-items:center;gap:14px}
.brand-mark{width:56px;height:56px;border-radius:50%;background:var(--green)}
.brand-name{font-size:19px;font-weight:600;line-height:1.3;color:var(--ink)}
.nav{position:absolute;left:548px;top:0;height:115px;display:flex}
.nav a{display:flex;align-items:flex-end;padding:0 20px 22px;font-size:15px;font-weight:600;color:var(--ink);text-decoration:none}
.nav a.active{background:var(--orange);color:var(--white);width:80px;justify-content:center;padding:0 0 22px}

/* hero */
.hero{top:115px;height:622px}
.hero-photo{position:absolute;inset:0;background:linear-gradient(180deg,#cfd6dc 0%,#9aa7b0 35%,#5d6c74 60%,#3b4246 100%)}
.hero-title{position:absolute;top:145px;width:100%;text-align:center;color:var(--white);font-size:56px;font-weight:800;line-height:1.05;letter-spacing:1px}
.hero-arrow{position:absolute;top:285px}
.hero-arrow.left{left:26px}.hero-arrow.right{right:26px}

/* welcome */
.welcome{top:737px;height:473px;text-align:center}
.section-title{font-size:48px;font-weight:800;color:var(--ink)}
.welcome .section-title{margin-top:56px}
.welcome p{width:680px;margin:18px auto 0;font-size:13.5px;line-height:1.55}
.welcome p:first-of-type{margin-top:26px}

/* about */
.about{top:1210px;height:608px}
.about-photo{position:absolute;inset:0;background:linear-gradient(90deg,#c9b79a 0%,#a89a7e 30%,#7f8a6a 60%,#93a07f 100%)}
.about-box{position:absolute;left:648px;top:115px;width:368px;height:395px;background:var(--green);color:var(--white);padding:70px 38px 0 38px}
.about-box h2{font-size:44px;font-weight:800}
.about-box p{margin-top:16px;font-size:13.5px;line-height:1.6}

/* team */
.team{top:1818px;height:657px;text-align:center}
.team .section-title{margin-top:88px}
.team-arrow{position:absolute;top:255px}
.team-arrow.left{left:100px}.team-arrow.right{right:100px}
.team-card{position:absolute;top:180px;width:200px;text-align:left}
.team-photo{position:relative;height:208px;background:linear-gradient(180deg,#e8eef3,#c7d2db)}
.team-photo::before{content:"";position:absolute;left:-8px;top:-8px;width:70px;height:70px;border-left:8px solid var(--c);border-top:8px solid var(--c)}
.team-card h3{margin-top:16px;font-size:16px;font-weight:700;color:var(--ink)}
.team-card p{margin-top:6px;font-size:11px;line-height:1.5}
.btn{display:inline-block;margin-top:18px;padding:7px 18px;border-radius:16px;background:var(--c);color:var(--white);font-size:11.5px;font-weight:600}

/* services */
.services{top:2475px;height:735px}
.services-photo{position:absolute;inset:0;background:linear-gradient(90deg,#7b7b7b 0%,#a09a94 40%,#8d8178 70%,#6e655f 100%)}
.services .section-title{position:absolute;top:52px;width:100%;text-align:center;color:var(--white)}
.service-list{position:absolute;left:174px;top:172px;width:270px;background:var(--white)}
.service-item{height:82px;display:flex;align-items:center;gap:14px;padding:0 16px;border-bottom:1px solid #ddd;font-size:14px;font-weight:600;color:var(--ink)}
.service-item.active{background:var(--blue);color:var(--white)}
.service-icon{width:38px;height:38px;flex:none}
.service-detail{position:absolute;left:487px;top:198px;width:300px;color:var(--white)}
.service-detail h3{font-size:21px;font-weight:700;line-height:1.3}
.service-detail p{margin-top:22px;font-size:11px;line-height:1.55}

/* good reads */
.reads{top:3210px;height:725px;text-align:center}
.reads .section-title{margin-top:80px}
.read-card{position:absolute;left:171px;width:854px;height:220px;background:var(--card);display:flex;text-align:left}
.read-image{width:297px;flex:none;background:linear-gradient(135deg,#d8cbb4,#6c5a44)}
.read-body{padding:34px 32px 0}
.read-body h3{font-size:21px;font-weight:700;color:var(--ink)}
.read-body .author{margin-top:10px;font-size:15px;font-weight:700;color:var(--orange)}
.read-body p{margin-top:12px;font-size:11px;line-height:1.55}

/* appointment */
.appointment{top:3935px;height:470px}
.map{position:absolute;left:0;top:0;width:606px;height:470px;background:linear-gradient(135deg,#eef0ea,#dfe4db)}
.request{position:absolute;left:606px;top:0;width:594px;height:470px;background:var(--orange);padding:46px 0 0 58px;color:var(--white)}
.request h2{font-size:27px;font-weight:800;letter-spacing:.5px}
.field{width:362px;height:30px;margin-top:12px;background:var(--white);font-size:11px;color:#666;padding:8px 10px}
.request h2+.field{margin-top:22px}
.field.message{height:78px}
.request .note{margin-top:12px;font-size:12px}
.submit{display:inline-block;margin-top:14px;padding:9px 26px;border-radius:18px;background:var(--blue);font-size:13px;font-weight:700}

/* footer */
.site-footer{top:4405px;height:187px;background:var(--footer);color:#ddd}
.contact{position:absolute;top:50px;display:flex;gap:14px;font-size:13px;line-height:1.6}
.footer-brand{position:absolute;left:930px;top:30px;width:110px;text-align:center;font-size:11px;font-weight:600}
.footer-brand .brand-mark{margin:0 auto 8px;width:60px;height:60px}
.copyright{position:absolute;left:172px;top:155px;font-size:11px}
</style>
</head>
<body>

<header class="site-header">
  <div class="brand"><span class="brand-mark"></span><span class="brand-name">Dr Halvorsen<br>Serenity Center</span></div>
  <nav class="nav">
    <a class="active">Home</a><a>About Us</a><a>Services</a><a>Good Reads</a><a>Contact</a>
  </nav>
</header>

<section class="hero">
  <div class="hero-photo" role="img" aria-label="Woman sitting on a dock looking out over a calm mountain lake"></div>
  <h1 class="hero-title">DR HALVORSEN<br>SERENITY CENTER</h1>
  <svg class="hero-arrow left" width="24" height="48" viewBox="0 0 24 48"><path d="M20 4 4 24l16 20" fill="none" stroke="#fff" stroke-width="2"/></svg>
  <svg class="hero-arrow right" width="24" height="48" viewBox="0 0 24 48"><path d="M4 4l16 20L4 44" fill="none" stroke="#fff" stroke-width="2"/></svg>
</section>

<section class="welcome">
  <h2 class="section-title">Welcome!</h2>
  <p>Each individual is unique with unique personality and unique needs. Therefore we provide individual treatment customized for you or your child. Multiculturalism also informs our practice. We are a full service mental health practice with the capacity to serve adults, children, teens and their parents.</p>
  <p>We provide high quality evidence-based treatment and care including medication management, pharmacogenomic testing, individual psychotherapy, group psychotherapy, art therapy, CBT, DBT and trauma therapy. Our providers are experts in treating variety of illnesses such as depression, anxiety, schizophrenia, ADHD, gender identity concerns and PTSD.</p>
  <p>We are experienced in a variety of methods that help people achieve their psychological goals, and we will discuss with you the best ways to attain the health and wellness that you deserve. We are committed to helping you achieve your optimal level of emotional functioning and fulfill a successful life.</p>
</section>

<section class="about">
  <div class="about-photo" role="img" aria-label="Woman meditating cross-legged on a yoga mat outdoors by a lake"></div>
  <div class="about-box">
    <h2>About Us</h2>
    <p>You will find a number of highly specialized – experienced and caring therapists and psychiatrists in Serenity Center. We provide medication management and psychotherapy (counseling) across the lifespan.<br>- children, teens and adults.</p>
  </div>
</section>

<section class="team">
  <h2 class="section-title">Meet The Team</h2>
  <svg class="team-arrow left" width="18" height="40" viewBox="0 0 18 40"><path d="M16 2 2 20l14 18" fill="none" stroke="#999" stroke-width="2"/></svg>
  <svg class="team-arrow right" width="18" height="40" viewBox="0 0 18 40"><path d="M2 2l14 18L2 38" fill="none" stroke="#999" stroke-width="2"/></svg>
  <div class="team-card" style="left:168px;--c:var(--green)">
    <div class="team-photo" role="img" aria-label="Portrait of a team doctor in a white coat"></div>
    <h3>Name:Loremus</h3>
    <p>At vero eos et accusamus et iusto dignissimos ducimus qui blanditiis praesentium voluptatum deleniti atque corrupti quos dolore.</p>
    <span class="btn">Make Appointment</span>
  </div>
  <div class="team-card" style="left:389px;--c:var(--blue)">
    <div class="team-photo" role="img" aria-label="Portrait of a team doctor in a white coat"></div>
    <h3>Name:Loremus</h3>
    <p>At vero eos et accusamus et iusto dignissimos ducimus qui blanditiis praesentium voluptatum deleniti atque corrupti quos dolore.</p>
    <span class="btn">Make Appointment</span>
  </div>
  <div class="team-card" style="left:609px;--c:var(--red)">
    <div class="team-photo" role="img" aria-label="Portrait of a team doctor in a white coat"></div>
    <h3>Name:Loremus</h3>
    <p>At vero eos et accusamus et iusto dignissimos ducimus qui blanditiis praesentium voluptatum deleniti atque corrupti quos dolore.</p>
    <span class="btn">Make Appointment</span>
  </div>
  <div class="team-card" style="left:829px;--c:var(--orange)">
    <div class="team-photo" role="img" aria-label="Portrait of a team doctor in a white coat"></div>
    <h3>Name:Loremus</h3>
    <p>At vero eos et accusamus et iusto dignissimos ducimus qui blanditiis praesentium voluptatum deleniti atque corrupti quos dolore.</p>
    <span class="btn">Make Appointment</span>
  </div>
</section>

<section class="services">
  <div class="services-photo" role="img" aria-label="Therapist listening to a smiling client during a session"></div>
  <h2 class="section-title">Our Services</h2>
  <div class="service-list">
    <div class="service-item"><svg class="service-icon" viewBox="0 0 38 38"><rect x="9" y="6" width="20" height="26" rx="3" fill="none" stroke="var(--orange)" stroke-width="2"/><path d="M14 19h10M19 14v10" stroke="var(--orange)" stroke-width="2"/></svg>Medication management</div>
    <div class="service-item active"><svg class="service-icon" viewBox="0 0 38 38"><path d="M4 24h30M8 24v6M30 24v6M10 20h14l6 4" fill="none" stroke="#fff" stroke-width="2"/><circle cx="12" cy="14" r="4" fill="none" stroke="#fff" stroke-width="2"/></svg>Psychotherapy: individual, group, couples, and family</div>
    <div class="service-item"><svg class="service-icon" viewBox="0 0 38 38"><path d="M6 32 26 12l4 4-20 20z" fill="none" stroke="var(--orange)" stroke-width="2"/><path d="M26 12l4-6 4 4-4 6" fill="none" stroke="var(--orange)" stroke-width="2"/></svg>Art Therapy</div>
    <div class="service-item"><svg class="service-icon" viewBox="0 0 38 38"><path d="M10 6v12a8 8 0 0 0 16 0V6M18 26v4a5 5 0 0 0 10 0v-4" fill="none" stroke="var(--green)" stroke-width="2"/><circle cx="28" cy="24" r="3" fill="none" stroke="var(--green)" stroke-width="2"/></svg>Treatment Approach</div>
    <div class="service-item"><svg class="service-icon" viewBox="0 0 38 38"><rect x="7" y="8" width="24" height="24" rx="3" fill="none" stroke="var(--red)" stroke-width="2"/><path d="M13 8V5h12v3M19 14v12M13 20h12" stroke="var(--red)" stroke-width="2" fill="none"/></svg>Treatment Areas</div>
  </div>
  <div class="service-detail">
    <h3>Psychotherapy:<br>Individual, group,<br>couples, and family</h3>
    <p>At vero eos et accusamus et iusto odio dignissimos ducimus qui blanditiis praesentium voluptatum deleniti atque corrupti quos dolores et quas molestias excepturi sint occaecati cupiditate non provident, similique sunt in culpa qui officia deserunt mollitia animi, id est laborum et dolorum fuga harum.</p>
    <p>At vero eos et accusamus et iusto odio dignissimos ducimus qui blanditiis praesentium voluptatum deleniti atque corrupti quos dolores et quas molestias excepturi sint occaecati cupiditate non provident.</p>
  </div>
</section>

<section class="reads">
  <h2 class="section-title">Good Reads</h2>
  <div class="read-card" style="top:156px">
    <div class="read-image" role="img" aria-label="Open book lying on a table"></div>
    <div class="read-body">
      <h3>At vero eos et accusamus et iissimos ducimu</h3>
      <div class="author">Author: Lorems</div>
      <p>At vero eos et accusamus et iusto odio dignissimos ducimus qui blanditiis praesentium voluptat um deleniti atque corrupti quos dolores et quas molestias excepturi sint occaecati cupiditate non provident, similique sunt in culpa qui officia deserunt mollitia animi, id est laborum et dolorum f uga. Et harum quidem rerum facilis est et expedita distinctio.</p>
    </div>
  </div>
  <div class="read-card" style="top:395px">
    <div class="read-body">
      <h3>At vero eos et accusamus et iissimos ducimu</h3>
      <div class="author">Author: Lorems</div>
      <p>At vero eos et accusamus et iusto odio dignissimos ducimus qui blanditiis praesentium voluptat um deleniti atque corrupti quos dolores et quas molestias excepturi sint occaecati cupiditate non provident, similique sunt in culpa qui officia deserunt mollitia animi, id est laborum et dolorum f uga. Et harum quidem rerum facilis est et expedita distinctio.</p>
    </div>
    <div class="read-image" role="img" aria-label="Hands holding an open book"></div>
  </div>
</section>

<section class="appointment">
  <div class="map" role="img" aria-label="Street map showing the clinic location"></div>
  <div class="request">
    <h2>APPOINTMENT REQUEST</h2>
    <div class="field">First Name</div>
    <div class="field">Last Name</div>
    <div class="field">Email Address</div>
    <div class="field">Phone Number</div>
    <div class="field message">Message</div>
    <p class="note">Please contact me for an appointment</p>
    <span class="submit">SUBMIT</span>
  </div>
</section>

<footer class="site-footer">
  <div class="contact" style="left:178px">
    <svg width="20" height="26" viewBox="0 0 20 26"><path d="M10 25S2 15 2 9a8 8 0 0 1 16 0c0 6-8 16-8 16z" fill="none" stroke="#ddd" stroke-width="1.6"/><circle cx="10" cy="9" r="3" fill="none" stroke="#ddd" stroke-width="1.6"/></svg>
    <div>4820 Maple Ridge Road, Suite 210,<br>Aurora, OH 44202</div>
  </div>
  <div class="contact" style="left:462px">
    <svg width="24" height="24" viewBox="0 0 24 24"><path d="M6 2l4 5-2 3a12 12 0 0 0 6 6l3-2 5 4-2 4C11 22 2 13 2 4z" fill="none" stroke="#ddd" stroke-width="1.6"/></svg>
    <div>Phone:<br>(440) 555-0142</div>
  </div>
  <div class="contact" style="left:650px">
    <svg width="36" height="26" viewBox="0 0 36 26"><rect x="1" y="2" width="34" height="22" fill="none" stroke="#ddd" stroke-width="1.6"/><path d="M1 2l17 13L35 2" fill="none" stroke="#ddd" stroke-width="1.6"/></svg>
    <div>Email<br>care@halvorsenserenity.com</div>
  </div>
  <div class="footer-brand"><div class="brand-mark"></div>Dr Halvorsen Serenity Center</div>
  <p class="copyright">© 2019 All Rights Are Reserved.Terms &amp; Conditions</p>
</footer>

</body>
</html>
```